Financial Services General Marketing Brochure

Need a brochure to help recipients understand what makes BWC unique and the services that we offer. Must match look/feel of website https://brightwellcustody.example Layouts should make it easy to read the content - content should not be crammed into a traditional size/layout. Please see attached creative brief for specifics.

Target Market(s)

Financial advisors and mature couples looking for trustee services.

Industry/Entity Type

Financial Service

Colors
34a7d8
ffc214

Requirements
Must have
• See Creative Brief

```html
<!DOCTYPE html>
<html lang="en">
<head>
<meta charset="utf-8">
<title>BWC Brochure Spread</title>
<link href="https://fonts.googleapis.com/css2?family=Libre+Baskerville:wght@400;700&family=Open+Sans:wght@400;600;700&display=swap" rel="stylesheet">
<style>
:root{
  --navy:#2f5a8e;
  --navy-deep:#264c7a;
  --gold:#e3a23a;
  --cream:#f5f2ec;
  --sand:#e6dccb;
  --ring:#d6c3a2;
  --paper:#fbfaf7;
  --ink:#3a3a3a;
  --bg:#dcdcdc;
}
*{box-sizing:border-box;margin:0;padding:0}
html,body{width:1200px;height:1000px;overflow:hidden;background:var(--bg)}
body{font-family:"Open Sans",Arial,sans-serif;color:var(--ink)}
.spread{position:absolute;left:50px;top:180px;width:1100px;height:640px;display:flex;box-shadow:0 12px 30px rgba(0,0,0,.18)}
.page{position:relative;width:550px;height:640px;overflow:hidden}
.page-left{display:flex}
.founder-column{width:270px;background:var(--navy);color:#fff}
.founder-photo{height:160px;background:linear-gradient(120deg,#6d5a3e,#2c3d55 55%,#8fa8c4)}
.founder-letter{padding:26px 24px 0 24px;font-size:11.5px;line-height:1.55}
.founder-letter p{margin-bottom:16px}
.dropcap{font-family:"Libre Baskerville",Georgia,serif;font-size:38px;float:left;line-height:1;margin:2px 6px 0 0}
.signature{margin-top:26px;text-align:right;font-size:11.5px;line-height:1.45}
.unique-column{width:280px;background:var(--cream)}
.unique-header{margin-top:70px;background:var(--sand);padding:16px 20px}
.unique-header h2{font-family:"Libre Baskerville",Georgia,serif;font-weight:400;color:var(--navy);font-size:17px}
.unique-list{padding:16px 22px}
.unique-item{margin-bottom:14px}
.unique-item h3{color:var(--gold);font-size:12.5px;font-weight:600;margin-bottom:3px}
.unique-item p{font-size:10.5px;line-height:1.45}
.page-right{background:var(--paper)}
.team-banner{margin-top:22px;height:84px;background:var(--navy);color:#fff;text-align:center;font-family:"Libre Baskerville",Georgia,serif;font-size:19px;line-height:1.35;padding-top:14px}
.team-diagram{position:absolute;left:0;top:106px}
.node-label{font-family:"Open Sans",Arial,sans-serif;font-weight:700;fill:var(--navy);font-size:14px;text-anchor:middle}
.node-sub{font-size:7.5px;fill:var(--navy);text-anchor:middle;font-family:"Open Sans",Arial,sans-serif}
.photo-caption{font-size:8px;font-weight:700;fill:#fff;text-anchor:middle;font-family:"Open Sans",Arial,sans-serif}
</style>
</head>
<body>
<div class="spread">
  <section class="page page-left">
    <div class="founder-column">
      <div class="founder-photo" role="img" aria-label="Photo of the founding principal in a suit"></div>
      <div class="founder-letter">
        <p><span class="dropcap">W</span>e understand that wealth and families is very complex. As families try to transfer wealth, it can be an incredible blessing or, if done improperly, can be incredibly destructive. Often a neutral third party is needed to come alongside the family's advisory team to provide guidance as families go through their wealth transition.</p>
        <p>Our relational focus and Open Architecture approach helps families to successfully navigate through the complexities of wealth, family and trusts. We believe a family "legacy" is about more than just money.</p>
        <div class="signature">Daniel Hale, J.D.<br>Founding Principal</div>
      </div>
    </div>
    <div class="unique-column">
      <div class="unique-header"><h2>What Makes BWC Unique</h2></div>
      <div class="unique-list">
        <div class="unique-item"><h3>Responsive</h3><p>The family deals directly with decision makers instead of being subject to committees with whom the family may never have the opportunity to interact or engage.</p></div>
        <div class="unique-item"><h3>Family Focus</h3><p>We help families successfully navigate the complexities of family wealth, not just perform trust administration.</p></div>
        <div class="unique-item"><h3>Independent</h3><p>To avoid any conflicts of interest, we have no formal affiliations with wealth management firms or financial advisory practices.</p></div>
        <div class="unique-item"><h3>Customized</h3><p>Together we develop a customized approach that will best suit the family's needs.</p></div>
        <div class="unique-item"><h3>Collaborative</h3><p>We work collaboratively with the family's team of trusted professionals.</p></div>
      </div>
    </div>
  </section>

  <section class="page page-right">
    <div class="team-banner">Brightwell Custody Group<br>Client/Family Centered Team</div>
    <svg class="team-diagram" width="550" height="534" viewBox="0 0 550 534">
      <defs>
        <linearGradient id="warm" x1="0" y1="0" x2="1" y2="1"><stop offset="0" stop-color="#c99a78"/><stop offset="1" stop-color="#5a3f30"/></linearGradient>
        <linearGradient id="light" x1="0" y1="0" x2="1" y2="1"><stop offset="0" stop-color="#f3e4da"/><stop offset="1" stop-color="#d9b8a4"/></linearGradient>
        <linearGradient id="couple" x1="0" y1="0" x2="1" y2="1"><stop offset="0" stop-color="#e8ddd3"/><stop offset="1" stop-color="#b9a79a"/></linearGradient>
      </defs>
      <g stroke="var(--ring)" stroke-width="2">
        <line x1="275" y1="250" x2="120" y2="260"/>
        <line x1="275" y1="250" x2="430" y2="150"/>
        <line x1="275" y1="250" x2="430" y2="300"/>
        <line x1="275" y1="250" x2="225" y2="400"/>
        <line x1="275" y1="250" x2="385" y2="420"/>
      </g>
      <g fill="#fff" stroke="var(--ring)" stroke-width="3">
        <circle cx="120" cy="260" r="56"/>
        <circle cx="430" cy="150" r="56"/>
        <circle cx="430" cy="300" r="56"/>
        <circle cx="225" cy="400" r="56"/>
        <circle cx="385" cy="420" r="56"/>
      </g>
      <g role="img" aria-label="Photo of a smiling young woman, the current beneficiary">
        <circle cx="165" cy="105" r="56" fill="url(#warm)" stroke="var(--ring)" stroke-width="3"/>
      </g>
      <text class="photo-caption" x="165" y="150">Current Beneficiary</text>
      <g role="img" aria-label="Photo of two young children, the future beneficiaries">
        <circle cx="300" cy="62" r="50" fill="url(#light)" stroke="var(--ring)" stroke-width="3"/>
      </g>
      <text class="photo-caption" x="300" y="100" fill="#555" style="fill:#555">Future Beneficiary</text>
      <g role="img" aria-label="Photo of a smiling senior couple, the trust creator">
        <polygon points="235,150 315,150 365,195 365,270 315,315 235,315 190,270 190,195" fill="url(#couple)"/>
      </g>
      <text class="photo-caption" x="278" y="302">Trust Creator</text>
      <text class="node-label" x="120" y="265">Attorney</text>
      <text class="node-label" x="430" y="155">Accountant</text>
      <text class="node-label" x="430" y="295">Trustee</text>
      <circle cx="430" cy="315" r="7" fill="var(--gold)"/>
      <text class="node-label" x="225" y="405">Financial</text>
      <text class="node-label" x="385" y="395" style="font-size:11px">Human Capital</text>
      <text class="node-label" x="385" y="409" style="font-size:11px">Resources</text>
      <text class="node-sub" x="385" y="422">Legacy Development</text>
      <text class="node-sub" x="385" y="432">Health Care Management</text>
      <text class="node-sub" x="385" y="442">Philanthropic Services</text>
      <text class="node-sub" x="385" y="452">Life Coaching</text>
    </svg>
  </section>
</div>
</body>
</html>
```